Toronto's Airline, based in Downtown looking for a whole new look and feel.

SkyMerrow is looking for a new look in our website. We are an airline based at Corwin Hale Airfield in Toronto. You can view our current website/services at www.skymerrow-example.com. We are expanding our services and look forward to a very sleek and modernized website. Please view the different pages on our website, we also need to add several new plane types as we have expanded and the website is not current. Would also be interesting to have a news feed or update feed through a widget which would be easy to use and update. we will also be implementing 2 third party programs called tavlo and quenbrook on the website, both are tour based and airline based sales and management functions.

Target Market(s)

Commuters, travel, tourism, dates, general public

Industry/Entity Type

Airline

Coding

Coded - Design and coding required

Number of Pages Required

5+ page

Font styles to use
Other font styles liked:
• Toronto subway font would be nice

Requirements
Must have
• A modern feel, easy to use, our booking function is currently a bit confusing which we will be working on. Content can be taken from our current website www.skymerrow-example.com
Nice to have
• work with out theme colours of blue and light grey

```html
<!DOCTYPE html>
<html lang="en">
<head>
<meta charset="utf-8">
<title>SkyMerrow Airways</title>
<link href="https://fonts.googleapis.com/css2?family=Open+Sans:wght@400;600;700;800&display=swap" rel="stylesheet">
<style>
:root{
  --blue:#1f5fbf;
  --blue-dark:#0f2f63;
  --navy:#132c55;
  --ink:#333;
  --muted:#777;
  --light:#f1f3f6;
  --line:#dde1e6;
  --footer:#2a2c30;
  --footer-dark:#1f2124;
  --white:#fff;
}
*{box-sizing:border-box;margin:0;padding:0}
html,body{width:1200px;height:3228px;overflow:hidden}
body{font-family:"Open Sans",Arial,sans-serif;color:var(--ink);background:var(--white)}
.page{width:1200px;height:3228px;position:relative}

/* header */
.site-header{height:68px;display:flex;align-items:center;justify-content:space-between;padding:0 48px 0 40px;background:var(--white);box-shadow:0 2px 6px rgba(0,0,0,.08);position:relative;z-index:2}
.brand{display:flex;align-items:center;gap:10px;background:var(--blue);padding:8px 14px;color:var(--white);font-weight:700;font-size:17px;letter-spacing:1px;text-transform:uppercase}
.brand-dot{width:14px;height:14px;border-radius:50%;background:var(--white)}
.main-nav{display:flex;align-items:center;gap:26px;font-size:12.5px;font-weight:700;color:#444}
.main-nav .active{color:var(--blue);border-bottom:2px solid var(--blue);padding-bottom:3px}
.btn{display:inline-block;background:var(--blue);color:var(--white);font-weight:700;font-size:12px;text-transform:uppercase;padding:9px 16px;border-radius:2px}
.btn-outline{background:var(--white);color:var(--ink);border:1px solid #999}

/* hero */
.hero{height:372px;position:relative;color:var(--white);text-align:center}
.hero-media{position:absolute;inset:0;background:linear-gradient(180deg,#0d1d3b 0%,#1d3e74 45%,#2c5a95 70%,#14284c 100%)}
.hero-content{position:relative;padding-top:70px}
.hero h1{font-size:46px;font-weight:800;letter-spacing:1px;text-transform:uppercase}
.hero p{font-size:14px;line-height:1.6;width:520px;margin:22px auto 0;font-weight:600}
.hero .btn{margin-top:32px;border-radius:4px;padding:11px 20px}

/* features */
.features{height:520px;text-align:center;padding-top:48px}
.section-title{color:var(--blue);font-size:24px;font-weight:800;text-transform:uppercase;letter-spacing:.5px}
.section-intro{font-size:12.5px;color:var(--muted);width:560px;margin:14px auto 0;line-height:1.6}
.feature-row{display:flex;justify-content:center;gap:130px;margin-top:40px}
.feature{width:240px}
.feature-icon{width:140px;height:140px;margin:0 auto;border-radius:50%;border:2px solid #555;display:flex;align-items:center;justify-content:center}
.feature-icon.is-main{background:var(--blue);border-color:var(--blue);box-shadow:0 0 0 6px #dbe6f6}
.feature h3{font-size:14px;font-weight:800;text-transform:uppercase;margin-top:26px}
.feature.is-main h3{color:var(--blue)}
.feature p{font-size:12px;color:var(--muted);line-height:1.6;margin-top:12px;min-height:58px}
.feature .btn{margin-top:14px;font-size:12px;text-transform:none;font-weight:600}

/* fleet */
.fleet{height:760px;background:var(--light);text-align:center;padding-top:84px}
.title-rule{width:60px;height:2px;background:var(--blue);margin:10px auto 0}
.card-row{display:flex;justify-content:center;gap:38px;margin-top:52px}
.card{width:310px;background:var(--white);box-shadow:0 2px 8px rgba(0,0,0,.1);padding-bottom:34px;position:relative}
.card-media{height:190px}
.card-badge{width:52px;height:52px;border-radius:50%;background:var(--white);position:absolute;top:164px;left:129px;display:flex;align-items:center;justify-content:center;box-shadow:0 1px 4px rgba(0,0,0,.15)}
.card h3{color:var(--blue);font-size:15px;font-weight:800;margin-top:44px}
.card p{font-size:12px;color:var(--muted);line-height:1.6;width:240px;margin:12px auto 0}
.card .btn{margin-top:18px;border:1px solid #999;background:var(--white);color:var(--ink);font-weight:600}

/* pricing */
.pricing{height:320px;background:linear-gradient(90deg,var(--navy),#1d4589);color:var(--white);display:flex;align-items:center;padding:0 96px;gap:70px}
.pricing-copy{width:520px}
.pricing h2{font-size:24px;font-weight:800;text-transform:uppercase}
.pricing p{font-size:12.5px;line-height:1.7;margin-top:14px;opacity:.9}
.pricing .btn{margin-top:28px;background:transparent;border:1px solid var(--white);text-transform:uppercase;font-size:11px}
.video{width:420px;height:250px;position:relative;border:3px solid rgba(255,255,255,.25)}
.video-media{position:absolute;inset:0;background:linear-gradient(135deg,#6b8fb8,#9db5cf 45%,#3c5f89)}
.video-bar{position:absolute;left:0;right:0;bottom:0;height:26px;background:rgba(0,0,0,.55);display:flex;align-items:center;padding:0 10px;gap:10px}
.video-track{flex:1;height:3px;background:rgba(255,255,255,.5)}

/* news */
.news{height:580px;text-align:center;padding-top:84px}
.news .section-title{color:var(--ink);letter-spacing:1px}
.news .section-intro{margin-top:16px}
.news-row{display:flex;justify-content:center;gap:44px;margin-top:86px;text-align:left}
.news-item{display:flex;gap:14px;width:310px}
.news-thumb{width:88px;height:70px;flex:none}
.news-item h4{font-size:14px;font-weight:700}
.news-item p{font-size:11px;color:var(--muted);line-height:1.5;margin-top:4px}
.news-item a{font-size:11px;color:var(--blue);font-weight:600;text-decoration:none;display:block;margin-top:4px}

/* agents */
.agents{height:200px;background:var(--light);display:flex;align-items:center;padding-left:40px;gap:70px;border-top:1px solid var(--line)}
.agents h2{color:var(--blue);font-size:24px;font-weight:800;text-transform:uppercase}
.agent{width:250px;height:90px;background:var(--white);border:1px solid var(--line);display:flex;align-items:center;justify-content:center;gap:10px;font-size:26px;font-weight:700;color:#2f3a4a}
.agent-mark{width:22px;height:22px;border-radius:50%;background:#2f3a4a}

/* footer */
.site-footer{height:328px;background:var(--footer);color:#ddd;display:flex;padding:46px 96px 0;gap:120px}
.contact h2{font-size:24px;font-weight:700;color:var(--white)}
.contact-list{list-style:none;margin-top:26px}
.contact-list li{display:flex;align-items:center;gap:16px;font-size:12.5px;margin-bottom:24px;line-height:1.5}
.contact-icon{width:40px;height:40px;border-radius:50%;background:#3a3d42;flex:none;display:flex;align-items:center;justify-content:center}
.contact-icon.is-pin{background:var(--blue)}
.form-area{flex:1}
.form-area p{font-size:15px;color:var(--white);margin-bottom:20px}
.form-grid{display:grid;grid-template-columns:1fr 1fr;gap:12px 14px}
.field{height:34px;background:#3a3d42;border:1px solid #4a4d52;font-size:11px;color:#999;padding:9px 10px}
.field.message{grid-column:1/3;height:78px}
.form-area .btn{margin-top:16px;font-size:11px;text-transform:none;font-weight:600}
.copyright{height:48px;background:var(--footer-dark);color:#aaa;font-size:11px;display:flex;align-items:center;justify-content:space-between;padding:0 96px}
.social{display:flex;gap:8px}
.social span{width:20px;height:20px;border-radius:50%;border:1px solid #888}
</style>
</head>
<body>
<div class="page">

<header class="site-header">
  <div class="brand"><span class="brand-dot"></span>SkyMerrow Airways</div>
  <nav class="main-nav">
    <span class="active">HOME</span><span>FLIGHTS</span><span>CHARTER &amp; FLEET</span><span>PACKAGES</span><span>GALLERY</span><span>CONTACT</span><span>FAQ</span>
    <span class="btn">Book Now</span>
  </nav>
</header>

<section class="hero">
  <div class="hero-media" role="img" aria-label="Night skyline of downtown Toronto with lit towers"></div>
  <div class="hero-content">
    <h1>SkyMerrow Airways</h1>
    <p>Looking For Something New And Exciting In Toronto? SkyMerrow Airways, A Private Airline Based At Corwin Hale Airfield In Downtown Toronto.</p>
    <span class="btn">Read More</span>
  </div>
</section>

<section class="features">
  <h2 class="section-title">Flights from Corwin Hale Airfield</h2>
  <p class="section-intro">Looking For Something New And Exciting In Toronto? SkyMerrow, A Private Airline Based At Corwin Hale Airfield In Downtown Toronto.</p>
  <div class="feature-row">
    <div class="feature">
      <div class="feature-icon">
        <svg width="60" height="60" viewBox="0 0 60 60" fill="none" stroke="#444" stroke-width="3"><rect x="10" y="20" width="40" height="28" rx="3"/><path d="M22 20v-7h16v7M10 32h40"/></svg>
      </div>
      <h3>VIP Business Travel</h3>
      <p>Say goodbye to check-in lines, baggage pick up, and customs. Arrive 15 minutes before departure, the aircraft is on your time.</p>
      <span class="btn btn-outline">Read More</span>
    </div>
    <div class="feature is-main">
      <div class="feature-icon is-main">
        <svg width="70" height="70" viewBox="0 0 70 70" fill="none" stroke="#fff" stroke-width="4"><circle cx="35" cy="35" r="26"/><path d="M23 36l8 8 16-17"/></svg>
      </div>
      <h3>Executive Class Terminal</h3>
      <p>Enjoy complimentary WiFi and coffee and tea in the private Harbor FBO Executive Terminal.</p>
      <span class="btn">Read More</span>
    </div>
    <div class="feature">
      <div class="feature-icon">
        <svg width="60" height="60" viewBox="0 0 60 60" fill="none" stroke="#444" stroke-width="3"><path d="M10 42a20 20 0 1 1 40 0"/><path d="M30 42l10-14"/><circle cx="30" cy="42" r="3" fill="#444"/></svg>
      </div>
      <h3>Saves You Time</h3>
      <p>Long drive to a destination without an international airport? Fly direct to a local airport, just a few kilometers.</p>
      <span class="btn btn-outline">Read More</span>
    </div>
  </div>
</section>

<section class="fleet">
  <h2 class="section-title">Charter and Fleet</h2>
  <div class="title-rule"></div>
  <div class="card-row">
    <article class="card">
      <div class="card-media" role="img" aria-label="Private aircraft parked inside a hangar" style="background:linear-gradient(160deg,#c9ced6,#8d96a3 60%,#5d6673)"></div>
      <div class="card-badge"><svg width="26" height="26" viewBox="0 0 24 24" fill="var(--blue)"><path d="M21 16v-2l-8-5V3.5a1.5 1.5 0 0 0-3 0V9l-8 5v2l8-2.5V19l-2 1.5V22l3.5-1 3.5 1v-1.5L13 19v-5.5z"/></svg></div>
      <h3>Our Flights</h3>
      <p>At SkyMerrow We Specialize In Short Range Affordable Air Taxi Transportation. Our Services Can Be Utilized For Business.</p>
      <span class="btn">View Pricing</span>
    </article>
    <article class="card">
      <div class="card-media" role="img" aria-label="Private jet on the runway under a clear sky" style="background:linear-gradient(180deg,#9fc0e3,#d8e3ee 60%,#8e959d)"></div>
      <div class="card-badge"><svg width="26" height="26" viewBox="0 0 24 24" fill="var(--blue)"><path d="M21 16v-2l-8-5V3.5a1.5 1.5 0 0 0-3 0V9l-8 5v2l8-2.5V19l-2 1.5V22l3.5-1 3.5 1v-1.5L13 19v-5.5z"/></svg></div>
      <h3>Private Charter</h3>
      <p>At SkyMerrow We Specialize In Short Range Affordable Air Taxi Transportation. Our Services Can Be Utilized For Business.</p>
      <span class="btn">View Pricing</span>
    </article>
    <article class="card">
      <div class="card-media" role="img" aria-label="Aircraft wing over clouds seen from a window" style="background:linear-gradient(180deg,#6f9fd4,#c7dbef 55%,#f2f4f6)"></div>
      <div class="card-badge"><svg width="26" height="26" viewBox="0 0 24 24" fill="var(--blue)"><path d="M21 16v-2l-8-5V3.5a1.5 1.5 0 0 0-3 0V9l-8 5v2l8-2.5V19l-2 1.5V22l3.5-1 3.5 1v-1.5L13 19v-5.5z"/></svg></div>
      <h3>Tours And Packages</h3>
      <p>At SkyMerrow We Specialize In Short Range Affordable Air Taxi Transportation. Our Services Can Be Utilized For Business.</p>
      <span class="btn">View Pricing</span>
    </article>
  </div>
</section>

<section class="pricing">
  <div class="pricing-copy">
    <h2>Pricing Guide</h2>
    <p>At SkyMerrow we specialize in short range affordable air taxi transportation. Our services are utilized for business and commuters traveling to the U.S. with destinations in ontario, quebec, new york, illinois, maine, michigan, washington, and massachusetts.</p>
    <span class="btn">View Price</span>
  </div>
  <div class="video">
    <div class="video-media" role="img" aria-label="Video still of the flight crew standing beside an aircraft"></div>
    <div class="video-bar">
      <svg width="10" height="12" viewBox="0 0 10 12" fill="#fff"><path d="M0 0l10 6-10 6z"/></svg>
      <span class="video-track"></span>
    </div>
  </div>
</section>

<section class="news">
  <h2 class="section-title">News Feed</h2>
  <p class="section-intro">Comparable To Airline Prices, You'd Be Surprised How Affordable It Really Is.</p>
  <div class="news-row">
    <article class="news-item">
      <div class="news-thumb" role="img" aria-label="Aircraft on the tarmac" style="background:linear-gradient(135deg,#7d8c9e,#c2cad4)"></div>
      <div><h4>Cheap Flights</h4><p>At SkyMerrow We Specialize In Short Range Affordable Air Taxi Transportation.</p><a>Read More &gt;&gt;</a></div>
    </article>
    <article class="news-item">
      <div class="news-thumb" role="img" aria-label="Aircraft cabin interior" style="background:linear-gradient(135deg,#5c6f88,#a9b6c6)"></div>
      <div><h4>Fantastic Savings</h4><p>At SkyMerrow We Specialize In Short Range Affordable Air Taxi Transportation.</p><a>Read More &gt;&gt;</a></div>
    </article>
    <article class="news-item">
      <div class="news-thumb" role="img" aria-label="Toronto waterfront skyline" style="background:linear-gradient(135deg,#4a76a8,#b7cde3)"></div>
      <div><h4>Different Rates</h4><p>At SkyMerrow We Specialize In Short Range Affordable Air Taxi Transportation.</p><a>Read More &gt;&gt;</a></div>
    </article>
  </div>
</section>

<section class="agents">
  <h2>Our Booking Agents:</h2>
  <div class="agent">quenbrook</div>
  <div class="agent"><span class="agent-mark"></span>tavlo</div>
</section>

<footer class="site-footer">
  <div class="contact">
    <h2>Contact Us</h2>
    <ul class="contact-list">
      <li><span class="contact-icon"><svg width="18" height="14" viewBox="0 0 18 14" fill="none" stroke="#fff" stroke-width="1.6"><rect x="1" y="1" width="16" height="12"/><path d="M1 1l8 7 8-7"/></svg></span>info@skymerrow-example.com</li>
      <li><span class="contact-icon is-pin"><svg width="14" height="18" viewBox="0 0 14 18" fill="#fff"><path d="M7 0a7 7 0 0 0-7 7c0 5 7 11 7 11s7-6 7-11a7 7 0 0 0-7-7zm0 9.5A2.5 2.5 0 1 1 7 4.5a2.5 2.5 0 0 1 0 5z"/></svg></span>Corwin Hale Airfield<br>Hangar 4, Suite 210 Toronto, Ontario<br>M0X 0A0</li>
      <li><span class="contact-icon"><svg width="16" height="16" viewBox="0 0 24 24" fill="#fff"><path d="M6.6 10.8a15 15 0 0 0 6.6 6.6l2.2-2.2a1 1 0 0 1 1-.25 11.4 11.4 0 0 0 3.6.6 1 1 0 0 1 1 1V20a1 1 0 0 1-1 1A17 17 0 0 1 3 4a1 1 0 0 1 1-1h3.5a1 1 0 0 1 1 1 11.4 11.4 0 0 0 .6 3.6 1 1 0 0 1-.25 1z"/></svg></span>1-800-555-0142</li>
    </ul>
  </div>
  <div class="form-area">
    <p>Fill out the form below, and we'll contact you shortly.</p>
    <div class="form-grid">
      <div class="field">First Name</div>
      <div class="field">Last Name</div>
      <div class="field">Phone Number</div>
      <div class="field">E-Mail Address</div>
      <div class="field message">Message</div>
    </div>
    <span class="btn">Send Now</span>
  </div>
</footer>
<div class="copyright">
  <span>Copyright © 2017 SkyMerrow Airways. All rights reserved</span>
  <div class="social"><span></span><span></span><span></span></div>
</div>

</div>
</body>
</html>
```